Web and Logo Design for eCommerce site

We're launching a sister brand and require a full design for the site.

The site must have an established feel and appeal to corporate and institutional buyers.
Updates

Just a note about the wireframe design:

The Search & Rescue / Coast Guard / NVDK, etc. in the header area aren't buttons or menu items, but rather just info (along the lines of a tagline).  Sort of a "who we serve" sort of thing.

Worth noting is that it's specifically geared towards LARGE BUYERS.  For example, a police force buying 200 headlamps and 85 pairs of gloves.  So they'll register + sign in and then add a bunch of items to a RFQ.

Aim for a professional, masculine design.

Target Market(s)

We will be selling outdoor gear to the military, law enforcement, fire and rescue and first responders.

Requirements
Must have
• We require:
- Logo (vector based)

Site:
- template page
* main site template, re-skinned version of our current site
* horizontal drop-down menu
- product listings page
* thumbnail view of products
- product details page
* including elements such as product image, color/size selector, descriptions and specs (again, based loosely on our current website)
- account management page
* illustrating basic data entry styles for text box, buttons, grid, etc.

The site needs to be given a responsive design, so 2 versions of each design should be presented for desktop + mobile views.

Additional funds are available if the designer is able to fully implement the designs into a responsive framework such as bootstrap.

Nice to have
• Clean, professional design similar to:

http://military.trailvexagear.com/gov/accessories/gloves.html

http://leaf.ombrivo.com/ProductFind.aspx?language=EN&category=Hardshell&subcat=Waterproof_Jackets

```html
<!DOCTYPE html>
<html lang="en">
<head>
<meta charset="utf-8">
<title>Bravalt – Northern Field Pro Supply</title>
<link href="https://fonts.googleapis.com/css2?family=Open+Sans:wght@400;600;700&display=swap" rel="stylesheet">
<style>
:root{
  --backdrop:#2a2520;
  --page:#ffffff;
  --ink:#2b2b2b;
  --muted:#666666;
  --line:#dddddd;
  --red:#d01a1a;
  --deep-red:#a30d0d;
  --dark:#1f1f1f;
  --panel-head:#2c3a44;
  --panel-head-2:#1b262d;
  --side-bg:#f2f2f2;
  --olive:#6b6a40;
  --sand:#8f8a63;
  --khaki:#a39c73;
}
*{box-sizing:border-box;margin:0;padding:0}
html,body{width:670px;height:1200px;overflow:hidden}
body{background:var(--backdrop);font-family:"Open Sans",Arial,sans-serif;color:var(--ink);position:relative}
.page{position:absolute;left:47px;top:26px;width:576px;height:1151px;background:var(--page)}
/* header */
.site-header{position:absolute;left:0;top:0;width:576px;height:62px}
.brand{position:absolute;left:16px;top:22px;display:flex;align-items:center;gap:6px}
.brand-mark{width:18px;height:18px;background:var(--red);border-radius:50%}
.brand-name{font-size:21px;font-weight:700;color:var(--red);line-height:1;letter-spacing:.5px}
.brand-tagline{position:absolute;left:40px;top:46px;font-size:5.6px;font-weight:600;letter-spacing:.4px;color:var(--dark);text-transform:uppercase}
.search{position:absolute;left:194px;top:26px;width:200px;height:21px;border:1px solid var(--line);font-size:7px;color:#999;padding:6px 6px}
.search svg{position:absolute;right:5px;top:5px}
.account-links{position:absolute;left:408px;top:35px;display:flex;gap:9px;font-size:7px;color:var(--muted)}
.account-links .signup{color:var(--red)}
.cart{position:absolute;left:561px;top:28px;width:28px;height:28px;border-radius:50%;background:var(--red);border:3px solid #fff;box-shadow:0 0 3px rgba(0,0,0,.3);display:flex;align-items:center;justify-content:center}
/* hero */
.hero{position:absolute;left:0;top:62px;width:576px;height:368px;overflow:hidden}
.hero-photo{position:absolute;inset:0;background:linear-gradient(180deg,#e9ece6 0%,#b9bfae 22%,#7b8656 45%,#5d6b34 70%,#3f4a22 100%)}
.hero-photo::after{content:"";position:absolute;left:300px;top:30px;width:230px;height:338px;background:radial-gradient(ellipse at 50% 50%,rgba(120,110,80,.55),rgba(120,110,80,0) 70%)}
.hero-fade{position:absolute;left:0;top:0;width:100%;height:52px;background:linear-gradient(180deg,rgba(255,255,255,.95),rgba(255,255,255,0))}
.serve-list{position:absolute;left:38px;top:10px;right:20px;display:flex;align-items:center;justify-content:space-between;font-size:7.2px;color:var(--dark);text-transform:uppercase}
.serve-list .label{background:var(--dark);color:#fff;padding:5px 10px;border:1px solid #000;border-radius:2px;box-shadow:inset 0 0 0 1px #555}
.hero-card{position:absolute;left:19px;top:118px;width:211px;height:170px;background:rgba(10,10,10,.88);padding:18px 13px}
.hero-title{font-size:19px;font-weight:400;color:#fff;line-height:1.18}
.hero-title span{color:var(--red)}
.hero-text{margin-top:11px;font-size:6.6px;line-height:1.55;color:#ddd}
.hero-btn{display:inline-block;margin-top:10px;background:#fff;color:var(--dark);font-size:7.6px;font-weight:600;padding:8px 12px;border-radius:2px}
.hero-dots{display:flex;gap:3px;margin-top:7px}
.hero-dots i{width:3px;height:3px;border-radius:50%;background:#fff}
.hero-dots i:first-child{background:var(--red)}
/* category tabs */
.tabs{position:absolute;left:0;top:430px;width:576px;height:44px;display:flex;align-items:center;justify-content:space-around;padding:0 12px;font-size:7.6px;color:var(--dark);box-shadow:0 6px 8px -6px rgba(0,0,0,.35)}
.tabs .active{color:var(--red)}
/* panels */
.panel-head{position:absolute;top:493px;height:27px;background:linear-gradient(180deg,var(--panel-head),var(--panel-head-2));color:#fff;font-size:11px;font-weight:600;padding:7px 5px;border-radius:4px 4px 0 0;text-transform:uppercase}
.sidebar-head{left:24px;width:128px}
.products-head{left:162px;width:390px}
.category-list{position:absolute;left:24px;top:520px;width:128px;list-style:none;background:var(--side-bg);border-right:1px solid var(--line)}
.category-list li{height:22.4px;font-size:6.8px;color:#444;padding:8px 4px 0;border-bottom:1px solid #d6d6d6}
/* product cards */
.product{position:absolute;width:118px;height:209px;border:1px solid var(--line);text-align:center;background:#fff}
.product-photo{display:block;margin:8px auto 0;width:82px;height:125px;border-radius:6px}
.photo-camo{background:linear-gradient(160deg,#a39c73,#7a7550 55%,#5f5c3d)}
.photo-khaki{background:linear-gradient(160deg,#9c946a,#7d7650)}
.photo-black{background:linear-gradient(160deg,#3a3a3a,#111)}
.photo-pants{background:linear-gradient(160deg,#b8ad8e,#8c8164);width:40px}
.photo-field{background:linear-gradient(160deg,#a89c7c,#7a6f55)}
.swatches{display:flex;justify-content:center;gap:2px;margin-top:8px}
.swatches i{width:7px;height:7px}
.sw-a{background:var(--olive)} .sw-b{background:var(--khaki)} .sw-c{background:#4b4a2e}
.product-name{font-size:6.4px;color:var(--muted);line-height:1.75;margin-top:3px;text-transform:uppercase}
.product-price{font-size:6.4px;color:var(--red)}
.product.featured{box-shadow:0 1px 4px rgba(0,0,0,.2)}
.price-badge{position:absolute;left:26px;top:70px;width:58px;height:58px;border-radius:50%;background:radial-gradient(circle at 40% 35%,var(--red),var(--deep-red));border:2px solid rgba(255,255,255,.6);color:#fff;font-size:10px;font-weight:600;line-height:1.3;display:flex;align-items:center;justify-content:center;text-align:center}
.add-cart{position:absolute;left:0;bottom:0;width:100%;height:34px;border-top:1px solid var(--line);display:flex;align-items:center;justify-content:center;gap:6px;font-size:9.6px;color:#555;background:linear-gradient(180deg,#fff,#f3f3f3)}
/* footer */
.site-footer{position:absolute;left:0;top:984px;width:576px;height:142px;border-top:1px solid var(--line)}
.footer-brand{position:absolute;left:16px;top:14px}
.footer-brand .brand-name{font-size:20px}
.footer-brand .brand-tagline{position:static;margin:3px 0 0 24px}
.offer-title{position:absolute;left:18px;top:62px;font-size:8.4px;font-weight:600;color:var(--dark)}
.offer-text{position:absolute;left:18px;top:80px;width:140px;font-size:6.2px;line-height:1.6;color:var(--muted)}
.subscribe{position:absolute;left:18px;top:110px;display:flex;height:21px}
.subscribe .field{width:106px;border:1px solid var(--line);font-size:6.6px;color:#bbb;padding:6px 4px}
.subscribe .go{width:35px;background:var(--deep-red);color:#fff;font-size:7.4px;display:flex;align-items:center;justify-content:center}
.footer-col{position:absolute;top:15px}
.footer-col h3{font-size:8.8px;font-weight:600;color:var(--dark);margin-bottom:7px}
.footer-col ul{list-style:none;font-size:7px;line-height:1.43;color:var(--muted)}
.col-nav{left:220px} .col-products{left:319px} .col-map{left:411px}
.map{width:144px;height:93px;background:linear-gradient(135deg,#e9e6dc,#d8d4c6)}
.legal{position:absolute;left:0;top:1126px;width:576px;height:25px;background:var(--dark);color:#ddd;font-size:6.4px;display:flex;align-items:center;justify-content:center}
</style>
</head>
<body>
<div class="page">
  <header class="site-header">
    <div class="brand"><span class="brand-mark"></span><span class="brand-name">Bravalt</span></div>
    <div class="brand-tagline">Northern Field Pro Supply</div>
    <div class="search">Search
      <svg width="10" height="10" viewBox="0 0 10 10"><circle cx="4" cy="4" r="3" fill="none" stroke="#999" stroke-width="1.2"/><line x1="6.3" y1="6.3" x2="9" y2="9" stroke="#999" stroke-width="1.4"/></svg>
    </div>
    <nav class="account-links"><span>Account</span><span>Wishlist</span><span>My Account</span><span class="signup">Sign Up</span></nav>
    <div class="cart">
      <svg width="12" height="12" viewBox="0 0 12 12"><path d="M2 4h8l-.8 7H2.8z" fill="#fff"/><path d="M4 4V3a2 2 0 0 1 4 0v1" fill="none" stroke="#fff" stroke-width="1.2"/></svg>
    </div>
  </header>

  <section class="hero">
    <div class="hero-photo" role="img" aria-label="Soldier in camouflage gear and helmet with backpack overlooking a river valley and mountains"></div>
    <div class="hero-fade"></div>
    <div class="serve-list">
      <span class="label">Who We Serve</span><span>Search &amp; Rescue</span><span>Coast Guard</span><span>NVDK</span><span>Fire</span><span>Military</span><span>Law Enforcement</span>
    </div>
    <div class="hero-card">
      <h1 class="hero-title"><span>NORTHERN</span> Field<br>Pro Supply</h1>
      <p class="hero-text">Lorem Ipsum is simply dummy text of the printing and typesetting industry. Lorem Ipsum has been the industry's standard dummy text ever since the 1500s, when an unknown printer.</p>
      <span class="hero-btn">LEARN MORE</span>
      <div class="hero-dots"><i></i><i></i><i></i></div>
    </div>
  </section>

  <nav class="tabs">
    <span class="active">Rescue Gear</span><span>Footwear</span><span>Clothing</span><span>Tents Mats</span><span>Sleeping Bags</span><span>Camping Gear</span><span>Snow Sports</span><span>Brands</span>
  </nav>

  <h2 class="panel-head sidebar-head">Category</h2>
  <ul class="category-list">
    <li>Rescue Gear</li><li>Footwear</li><li>Clothing</li><li>T.ents Mats Sleeping Bags</li><li>Camping Gear</li><li>Snow Sports</li><li>Brands</li><li>Coast Guard</li><li>NVDK</li><li>Fire</li><li>Military</li><li>Law Enforcement</li><li>Lorem Ipsum Dolor</li><li>Sit Amet Consectetur</li><li>Adipisicing Elit, Sed Do</li><li>Eiusmod Tempor</li><li>Incididunt Ut Labore</li><li>Et Dolore</li><li>Magna Aliqua.</li><li>Magna Aliqua</li>
  </ul>

  <h2 class="panel-head products-head">Bravalt Products</h2>

  <article class="product featured" style="left:162px;top:530px">
    <div class="product-photo photo-camo" role="img" aria-label="Camouflage hooded jacket"></div>
    <div class="price-badge">$750.00<br>CAD</div>
    <div class="swatches"><i class="sw-a"></i></div>
    <p class="product-name">Kestrel LT Jacket</p>
    <div class="add-cart">
      <svg width="13" height="11" viewBox="0 0 13 11"><path d="M0 1h2.5l1.5 6h7l1.5-4.5H4" fill="none" stroke="#333" stroke-width="1.2"/><circle cx="5" cy="9.5" r="1.1" fill="#333"/><circle cx="10" cy="9.5" r="1.1" fill="#333"/></svg>
      Add to Cart
    </div>
  </article>
  <article class="product" style="left:294px;top:530px">
    <div class="product-photo photo-camo" role="img" aria-label="Camouflage field jacket"></div>
    <div class="swatches"><i class="sw-a"></i><i class="sw-b"></i><i class="sw-c"></i></div>
    <p class="product-name">Kestrel LT Jacket<br>TerraCam Men's Gen 2 -<br>Revised</p>
    <p class="product-price">$750.00 CAD</p>
  </article>
  <article class="product" style="left:425px;top:530px">
    <div class="product-photo photo-khaki" role="img" aria-label="Khaki hooded shell jacket"></div>
    <div class="swatches"><i class="sw-a"></i><i class="sw-b"></i><i class="sw-c"></i></div>
    <p class="product-name">Kestrel LT Jacket<br>TerraCam Men's Gen 2 -<br>Revised</p>
    <p class="product-price">$750.00 CAD</p>
  </article>
  <article class="product" style="left:162px;top:751px">
    <div class="product-photo photo-black" role="img" aria-label="Black hooded shell jacket"></div>
    <div class="swatches"><i class="sw-a"></i></div>
    <p class="product-name">Kestrel LT Jacket<br>TerraCam Men's Gen 2 -<br>Revised</p>
    <p class="product-price">$750.00 CAD</p>
  </article>
  <article class="product" style="left:294px;top:751px">
    <div class="product-photo photo-pants" role="img" aria-label="Camouflage field trousers"></div>
    <div class="swatches"><i class="sw-a"></i><i class="sw-c"></i><i class="sw-b"></i></div>
    <p class="product-name">Kestrel LT Jacket<br>TerraCam Men's Gen 2 -<br>Revised</p>
    <p class="product-price">$750.00 CAD</p>
  </article>
  <article class="product" style="left:425px;top:751px">
    <div class="product-photo photo-field" role="img" aria-label="Camouflage combat shirt"></div>
    <div class="swatches"><i class="sw-c"></i><i class="sw-a"></i><i class="sw-b"></i></div>
    <p class="product-name">Kestrel LT Jacket<br>TerraCam Men's Gen 2 -<br>Revised</p>
    <p class="product-price">$750.00 CAD</p>
  </article>

  <footer class="site-footer">
    <div class="footer-brand">
      <div class="brand" style="position:static"><span class="brand-mark"></span><span class="brand-name">Bravalt</span></div>
      <div class="brand-tagline">Northern Field Pro Supply</div>
    </div>
    <p class="offer-title">Get informed for our Special offers</p>
    <p class="offer-text">Get the best and most interesting discount offers via email.</p>
    <div class="subscribe"><span class="field">you@example.com</span><span class="go">Enter</span></div>
    <div class="footer-col col-nav">
      <h3>Navigation</h3>
      <ul><li>Rescue Gear</li><li>Footwear</li><li>Clothing</li><li>Tents Mats</li><li>Sleeping Bags</li><li>Camping Gear</li><li>Snow Sports</li><li>Brands</li></ul>
    </div>
    <div class="footer-col col-products">
      <h3>Products</h3>
      <ul><li>Rescue Gear</li><li>Footwear</li><li>Clothing</li><li>Tents Mats</li><li>Sleeping Bags</li><li>Camping Gear</li><li>Snow Sports</li><li>Brands</li></ul>
    </div>
    <div class="footer-col col-map">
      <h3>Map</h3>
      <div class="map" role="img" aria-label="Street map showing the store location"></div>
    </div>
  </footer>
  <div class="legal">CopyRight © 2014 BRAVALT All Received</div>
</div>
</body>
</html>
```